English and Spanish Language School Needs a Business Card

Need a business card design a startup company called Maribel Language School. The company will offer English and Spanish conversational level courses designed to make the learner feel comfortable with grammar and vocabulary. We would like to see a logo with some colour that should communicate learning, growth.

Target Market(s)

Consumers and businesses

Industry/Entity Type

Education

Contact Information for Business Card

TBD

Font styles to use
Serif

Requirements
Must have
• Include the following
• Logo
• Name
• Title
• Cellphone Number
• Office Phone number
• Email address
• Office Address

```html
<!DOCTYPE html>
<html lang="en">
<head>
<meta charset="utf-8">
<title>Maribel Language School – Business Card</title>
<link rel="stylesheet" href="https://fonts.googleapis.com/css2?family=Montserrat:wght@400;600;700&display=swap">
<style>
  :root {
    --stage: #ecebe8;
    --card-white: #ffffff;
    --brand-red: #c8202d;
    --brand-red-light: #e04450;
    --brand-red-deep: #a5131d;
    --ink-dark: #1f2d2a;
    --text-on-red: #ffffff;
    --detail-ink: #3a1013;
  }
  * { box-sizing: border-box; margin: 0; padding: 0; }
  html, body {
    width: 1200px; height: 913px; overflow: hidden;
    background: var(--stage);
    font-family: "Montserrat", sans-serif;
  }
  .canvas {
    position: relative; width: 1200px; height: 913px;
    display: flex; align-items: center; justify-content: center; gap: 40px;
  }
  .card {
    position: relative; width: 540px; height: 309px;
    border-radius: 14px; overflow: hidden;
    box-shadow: 0 6px 18px rgba(0,0,0,0.18);
  }
  .card-front { background: var(--card-white); }
  .card-front .wave { position: absolute; inset: 0; width: 100%; height: 100%; }
  .front-brand {
    position: absolute; left: 30px; top: 124px;
    color: var(--brand-red); font-weight: 700; line-height: 1.05;
  }
  .front-brand .brand-main { display: block; font-size: 44px; letter-spacing: -1px; }
  .front-brand .brand-sub { display: block; font-size: 15px; padding-left: 4px; }
  .contact {
    position: absolute; right: 26px; top: 42px; text-align: right;
    color: var(--detail-ink); font-size: 11.5px; line-height: 1.45;
  }
  .contact .person-name { color: var(--text-on-red); font-size: 21px; font-weight: 700; line-height: 1.1; }
  .contact .person-title { color: var(--detail-ink); font-size: 12px; margin-bottom: 6px; }
  .contact .row { display: flex; justify-content: flex-end; align-items: center; gap: 8px; }
  .contact .row .icon { width: 10px; height: 10px; flex: none; }
  .contact .web { font-weight: 700; }
  .card-back {
    background: linear-gradient(160deg, var(--brand-red-light) 0%, var(--brand-red) 45%, var(--brand-red-deep) 100%);
  }
  .back-brand {
    position: absolute; left: 0; right: 0; top: 96px; text-align: center;
    color: var(--text-on-red); font-weight: 700; line-height: 1.05;
  }
  .back-brand .brand-main { display: block; font-size: 64px; letter-spacing: -1.5px; }
  .back-brand .brand-sub { display: block; font-size: 20px; }
  .back-url {
    position: absolute; right: 40px; bottom: 34px;
    color: var(--text-on-red); font-size: 13px; font-weight: 600; letter-spacing: 0.3px;
  }
</style>
</head>
<body>
<main class="canvas">
  <section class="card card-front" aria-label="Business card front">
    <svg class="wave" viewBox="0 0 540 309" preserveAspectRatio="none" aria-hidden="true">
      <defs>
        <linearGradient id="redPanel" x1="0" y1="0" x2="0.4" y2="1">
          <stop offset="0" stop-color="#e04450"/>
          <stop offset="0.5" stop-color="#c8202d"/>
          <stop offset="1" stop-color="#a5131d"/>
        </linearGradient>
      </defs>
      <path d="M352 0 C330 110 290 220 226 309 L212 309 C278 220 318 110 340 0 Z" fill="#1f2d2a"/>
      <path d="M366 0 C344 110 304 220 240 309 L540 309 L540 0 Z" fill="url(#redPanel)"/>
    </svg>
    <div class="front-brand">
      <span class="brand-main">Maribel</span>
      <span class="brand-sub">Language School</span>
    </div>
    <div class="contact">
      <p class="person-name">Lena Hartwell</p>
      <p class="person-title">Director</p>
      <p>PO Box 218</p>
      <p>Brookfield VIC 3920</p>
      <p class="row">+330 2400-1187
        <svg class="icon" viewBox="0 0 10 10" aria-hidden="true"><rect x="2.5" y="0.5" width="5" height="9" rx="1" fill="none" stroke="currentColor"/><circle cx="5" cy="8" r="0.6" fill="currentColor"/></svg>
      </p>
      <p class="row">+330 2400-5519
        <svg class="icon" viewBox="0 0 10 10" aria-hidden="true"><path d="M2 1 L4 1 L4.6 3 L3.4 4 C4 5.4 4.8 6.2 6 6.7 L7 5.5 L9 6.2 L9 8.2 C5 8.6 1.4 5 1.8 1 Z" fill="currentColor"/></svg>
      </p>
      <p class="row">hello@maribelschool.com
        <svg class="icon" viewBox="0 0 10 10" aria-hidden="true"><rect x="0.5" y="2" width="9" height="6" fill="none" stroke="currentColor"/><path d="M0.5 2 L5 5.5 L9.5 2" fill="none" stroke="currentColor"/></svg>
      </p>
      <p class="row web">maribelschool.com
        <svg class="icon" viewBox="0 0 10 10" aria-hidden="true"><circle cx="5" cy="5" r="4.3" fill="none" stroke="currentColor"/><ellipse cx="5" cy="5" rx="1.8" ry="4.3" fill="none" stroke="currentColor"/><path d="M0.7 5 H9.3" stroke="currentColor"/></svg>
      </p>
    </div>
  </section>

  <section class="card card-back" aria-label="Business card back">
    <div class="back-brand">
      <span class="brand-main">Maribel</span>
      <span class="brand-sub">Language School</span>
    </div>
    <p class="back-url">www.maribelschool.com</p>
  </section>
</main>
</body>
</html>
```